2021 Summer Ads Hollis Bay Custom Homes

We need a re-design of our summer ad run for our customer, Hollis Bay Custom Homes. They are custom home builders in the mostly rural parts of West Virginia, USA. They are known for their "Forever Home" tagline. We'd like two designed ads with the main difference being just the custom home that's featured. These designs should be for a Zintrola banner like 300 x 250 and square ad like 250 x 250. For inspiration please visit the Hollis Bay Custom Homes website at www dot hollisbaycustomhomes dot com

Target Market(s)

consumers / new home shoppers

Industry/Entity Type

Consumer

Requirements
Must have
• HBCH logo
Price Lock Available!
Custom home pic
Learn more >
small CFRM logo mark

```html
<!DOCTYPE html>
<html lang="en">
<head>
<meta charset="utf-8">
<title>Hollis Bay Custom Homes – Summer Ads</title>
<link rel="stylesheet" href="https://fonts.googleapis.com/css2?family=Open+Sans:wght@400;600;700&display=swap">
<style>
  :root {
    --page: #ffffff;
    --ink-black: #050505;
    --brand-red: #c8363a;
    --deep-red: #a3232a;
    --cta-red: #e0141c;
    --white: #ffffff;
    --logo-red: #9b1c22;
    --badge-blue: #1f3f8a;
  }
  * { box-sizing: border-box; margin: 0; padding: 0; }
  html, body {
    width: 1200px; height: 589px; overflow: hidden;
    background: var(--page);
    font-family: "Open Sans", Arial, sans-serif;
  }
  .canvas { position: relative; width: 1200px; height: 589px; }
  .ad {
    position: absolute; top: 42px;
    width: 300px; height: 250px;
    transform-origin: 0 0; transform: scale(1.906);
    overflow: hidden;
    box-shadow: 0 0 1px rgba(0,0,0,.25);
  }
  .ad--banner { left: 51px; }
  .ad--square { left: 667px; width: 250px; background: var(--brand-red); }

  .ad__art { position: absolute; inset: 0; width: 100%; height: 100%; }

  .logo-badge {
    position: absolute; display: flex; align-items: center; justify-content: center;
    background: var(--white);
  }
  .logo-badge__name {
    color: var(--logo-red); font-weight: 700; letter-spacing: .3px; white-space: nowrap;
  }
  .ad--banner .logo-badge {
    left: 223px; top: 46px; width: 62px; height: 44px; border-radius: 50%;
  }
  .ad--banner .logo-badge__name { font-size: 8px; }
  .ad--square .logo-badge {
    left: 8px; top: 44px; width: 102px; height: 56px; border-radius: 3px;
  }
  .ad--square .logo-badge__name { font-size: 12px; }

  .partner-badge {
    position: absolute; border-radius: 50%; background: var(--white);
    border: 2px solid var(--badge-blue);
  }
  .ad--banner .partner-badge { left: 228px; top: 99px; width: 50px; height: 40px; }
  .ad--square .partner-badge { left: 210px; top: 219px; width: 28px; height: 22px; border-width: 1.5px; }

  .ad__copy { position: absolute; color: var(--white); }
  .ad__tagline { font-weight: 600; }
  .ad__headline { font-weight: 700; line-height: 1.15; }
  .ad__cta {
    display: inline-block; font-weight: 700; text-decoration: underline;
    text-underline-offset: 2px;
  }
  .ad--banner .ad__copy { left: 118px; top: 164px; }
  .ad--banner .ad__tagline { font-size: 13.5px; margin-bottom: 9px; }
  .ad--banner .ad__headline { font-size: 16px; margin-bottom: 7px; }
  .ad--banner .ad__cta { font-size: 13.5px; color: var(--cta-red); }

  .ad--square .ad__copy { left: 15px; top: 112px; }
  .ad--square .ad__tagline { font-size: 13px; margin-bottom: 3px; }
  .ad--square .ad__headline { font-size: 22px; margin-bottom: 8px; }
  .ad--square .ad__cta { font-size: 11.5px; color: var(--white); }
</style>
</head>
<body>
<main class="canvas">

  <section class="ad ad--banner" aria-label="Hollis Bay Custom Homes banner ad">
    <svg class="ad__art" viewBox="0 0 300 250" preserveAspectRatio="none">
      <defs>
        <linearGradient id="barnScene" x1="0" y1="0" x2="0.4" y2="1">
          <stop offset="0" stop-color="#7fb4e6"/>
          <stop offset="0.35" stop-color="#cfd8df"/>
          <stop offset="0.6" stop-color="#8a8f95"/>
          <stop offset="1" stop-color="#4e7a3a"/>
        </linearGradient>
      </defs>
      <rect width="300" height="250" fill="url(#barnScene)" role="img"
            aria-label="Photo of a white custom home with a cupola and dark roof among green trees"/>
      <path d="M160,0 C192,60 132,110 112,140 C88,172 74,210 78,250 L300,250 L300,0 Z" fill="var(--deep-red)"/>
      <path d="M168,0 C200,60 140,112 120,142 C96,174 82,212 86,250 L300,250 L300,0 Z" fill="var(--ink-black)"/>
    </svg>
    <div class="logo-badge"><span class="logo-badge__name">HOLLIS BAY</span></div>
    <div class="partner-badge" role="img" aria-label="Partner association badge"></div>
    <div class="ad__copy">
      <p class="ad__tagline">Forever Home</p>
      <p class="ad__headline">Price Lock Available!</p>
      <a class="ad__cta" href="#">Learn More &gt;</a>
    </div>
  </section>

  <section class="ad ad--square" aria-label="Hollis Bay Custom Homes square ad">
    <svg class="ad__art" viewBox="0 0 250 250" preserveAspectRatio="none">
      <defs>
        <linearGradient id="garageScene" x1="0" y1="0" x2="0.3" y2="1">
          <stop offset="0" stop-color="#5f8f3e"/>
          <stop offset="0.3" stop-color="#8a949c"/>
          <stop offset="0.6" stop-color="#a6302c"/>
          <stop offset="1" stop-color="#9a9690"/>
        </linearGradient>
      </defs>
      <path d="M172,0 L250,0 L250,250 L124,250 Z" fill="var(--white)"/>
      <path d="M178,0 L250,0 L250,250 L131,250 Z" fill="url(#garageScene)" role="img"
            aria-label="Photo of a red detached garage with white doors and a cupola"/>
    </svg>
    <div class="logo-badge"><span class="logo-badge__name">HOLLIS BAY</span></div>
    <div class="partner-badge" role="img" aria-label="Partner association badge"></div>
    <div class="ad__copy">
      <p class="ad__tagline">Forever Home</p>
      <p class="ad__headline">Price Lock<br>Available!</p>
      <a class="ad__cta" href="#">Learn More &gt;</a>
    </div>
  </section>

</main>
</body>
</html>
```